KDWB Business Card

Looking for a business card design to incorporate our branding. We want to only use the colors listing in the Branding Package (attached).
Updates

Target Market(s)

People who need their phone or device fixed.

Industry/Entity Type

Electronics

Contact Information for Business Card

Please use:

Brightwick Gadget Clinic LLC
4810 E Harlow Ridge Rd
Suite 417
San Antonio, TX 78163

Marcus Delgrove, Store Manager

(210) 555-0147

Requirements
Must have
• Must include the colors that are contained within the Branding Package PDF file.

```html
<!DOCTYPE html>
<html lang="en">
<head>
<meta charset="utf-8">
<title>Brightwick Gadget Clinic – Business Card</title>
<link href="https://fonts.googleapis.com/css2?family=Roboto:wght@300;400&display=swap" rel="stylesheet">
<style>
  :root {
    --orange: #f15a22;
    --black: #1b1b1b;
    --white: #ffffff;
    --ink: #2b2b2b;
    --grey-band: #4d4d4f;
    --rule: #8a8a8a;
    --backdrop: #e6e6e6;
  }
  html, body {
    margin: 0;
    padding: 0;
    width: 1200px;
    height: 810px;
    overflow: hidden;
    background: var(--backdrop);
    font-family: "Roboto", Arial, sans-serif;
  }
  .canvas {
    position: relative;
    width: 1200px;
    height: 810px;
  }
  .card {
    position: absolute;
    width: 540px;
    height: 309px;
    border-radius: 16px;
    overflow: hidden;
    box-shadow: 0 6px 18px rgba(0,0,0,0.18);
  }
  .card--front {
    left: 40px;
    top: 120px;
    background: var(--black);
  }
  .card--back {
    left: 620px;
    top: 381px;
    background: var(--white);
  }
  .brand {
    position: absolute;
    display: flex;
    align-items: center;
    gap: 12px;
  }
  .brand__mark {
    width: 44px;
    height: 44px;
    border-radius: 9px;
    background: var(--orange);
    flex: none;
  }
  .brand__name {
    font-weight: 300;
    font-size: 27px;
    line-height: 1.1;
    color: var(--orange);
    letter-spacing: 0.2px;
  }
  .card--front .brand {
    left: 110px;
    top: 128px;
  }
  .card--back .brand {
    left: 36px;
    top: 100px;
  }
  .card--back .brand__name {
    font-size: 22px;
  }
  .divider {
    position: absolute;
    left: 300px;
    top: 70px;
    width: 1px;
    height: 150px;
    background: var(--rule);
  }
  .contact {
    position: absolute;
    left: 322px;
    top: 78px;
    color: var(--ink);
  }
  .contact__name {
    font-size: 17px;
    font-weight: 400;
    margin: 0;
  }
  .contact__title {
    font-size: 11px;
    color: var(--orange);
    margin: 2px 0 22px 52px;
  }
  .contact__row {
    display: flex;
    align-items: center;
    gap: 8px;
    font-size: 12.5px;
    font-weight: 400;
    margin-bottom: 7px;
    white-space: nowrap;
  }
  .contact__row--phone {
    margin-bottom: 18px;
    font-size: 14px;
  }
  .icon {
    width: 13px;
    height: 13px;
    flex: none;
  }
  .band {
    position: absolute;
    left: 0;
    bottom: 0;
    width: 100%;
    height: 44px;
    background: var(--grey-band);
    border-top: 3px solid var(--orange);
  }
</style>
</head>
<body>
<main class="canvas">

  <section class="card card--front" aria-label="Card front">
    <div class="brand">
      <span class="brand__mark"></span>
      <span class="brand__name">Brightwick Gadget Clinic</span>
    </div>
  </section>

  <section class="card card--back" aria-label="Card back">
    <div class="brand">
      <span class="brand__mark"></span>
      <span class="brand__name">Brightwick<br>Gadget Clinic</span>
    </div>

    <div class="divider"></div>

    <div class="contact">
      <p class="contact__name">Marcus Delgrove</p>
      <p class="contact__title">Store Manager</p>

      <div class="contact__row contact__row--phone">
        <svg class="icon" viewBox="0 0 13 13" aria-hidden="true">
          <rect width="13" height="13" rx="2" fill="#f15a22"/>
          <path d="M4 2.5 L5.5 4.5 L4.7 5.5 Q5.5 7.5 7.5 8.3 L8.5 7.5 L10.5 9 L9.5 10.5 Q5 10 2.5 4 Z" fill="#fff"/>
        </svg>
        <span>(210) 555-0147</span>
      </div>

      <div class="contact__row">
        <svg class="icon" viewBox="0 0 13 13" aria-hidden="true">
          <rect width="13" height="13" rx="2" fill="#f15a22"/>
          <rect x="2.5" y="3.5" width="8" height="6" fill="none" stroke="#fff" stroke-width="1"/>
          <path d="M2.5 3.5 L6.5 7 L10.5 3.5" fill="none" stroke="#fff" stroke-width="1"/>
        </svg>
        <span>marcus@BrightwickClinic.com</span>
      </div>

      <div class="contact__row">
        <svg class="icon" viewBox="0 0 13 13" aria-hidden="true">
          <rect width="13" height="13" rx="2" fill="#f15a22"/>
          <circle cx="6.5" cy="6.5" r="3.8" fill="none" stroke="#fff" stroke-width="1"/>
          <path d="M2.7 6.5 H10.3 M6.5 2.7 Q4.5 6.5 6.5 10.3 M6.5 2.7 Q8.5 6.5 6.5 10.3" fill="none" stroke="#fff" stroke-width="0.8"/>
        </svg>
        <span>www.BrightwickClinic.com</span>
      </div>
    </div>

    <div class="band"></div>
  </section>

</main>
</body>
</html>
```